Business Card Design Project

Business card based on attached logo

Todd Merrick
Todd@lorvantest.com
877-514-9073 ext. 318
Www.LorvanTest.com

Industry/Entity Type

Business

```html
<!DOCTYPE html>
<html lang="en">
<head>
<meta charset="utf-8">
<title>LorvanTest Business Cards</title>
<link href="https://fonts.googleapis.com/css2?family=Roboto:wght@400;500;700&display=swap" rel="stylesheet">
<style>
  :root {
    --stage: #8b5230;
    --paper: #ffffff;
    --brand-red: #ec1c24;
    --ink: #231f20;
    --text: #2b2b2b;
    --rule: #bdbdbd;
  }
  html, body {
    margin: 0;
    padding: 0;
    width: 1200px;
    height: 715px;
    overflow: hidden;
  }
  body {
    font-family: "Roboto", Arial, sans-serif;
    background: var(--stage);
  }
  .canvas {
    position: relative;
    width: 1200px;
    height: 715px;
    overflow: hidden;
    background: var(--stage);
  }
  .card {
    position: absolute;
    width: 509px;
    height: 291px;
    overflow: hidden;
    box-shadow: 0 1px 3px rgba(0,0,0,0.35);
  }
  .card--front { left: 50px; top: 35px; background: var(--paper); }
  .card--back-white { left: 623px; top: 36px; background: var(--paper); }
  .card--back-red { left: 47px; top: 378px; background: var(--brand-red); }
  .card--back-black { left: 628px; top: 381px; background: var(--ink); }

  /* Front card */
  .brand {
    position: absolute;
    left: 44px;
    top: 110px;
    display: flex;
    align-items: center;
    gap: 8px;
  }
  .brand__mark {
    width: 18px;
    height: 18px;
    background: var(--brand-red);
  }
  .brand__name {
    font-weight: 700;
    font-size: 34px;
    color: var(--ink);
    letter-spacing: -0.5px;
  }
  .divider {
    position: absolute;
    left: 282px;
    top: 80px;
    width: 1px;
    height: 116px;
    background: var(--rule);
  }
  .contact {
    position: absolute;
    left: 294px;
    top: 82px;
  }
  .contact__name {
    margin: 0 0 14px;
    font-weight: 700;
    font-size: 19px;
    letter-spacing: 0.6px;
    color: var(--brand-red);
  }
  .contact__list {
    list-style: none;
    margin: 0;
    padding: 0;
  }
  .contact__item {
    display: flex;
    align-items: center;
    gap: 6px;
    font-size: 13.5px;
    color: var(--text);
    margin-bottom: 7px;
  }
  .contact__icon {
    width: 11px;
    height: 11px;
    flex: none;
  }
  .front-rule {
    position: absolute;
    left: 0;
    top: 258px;
    width: 100%;
    height: 2px;
    background: var(--ink);
  }
  .front-band {
    position: absolute;
    left: 0;
    top: 264px;
    width: 100%;
    height: 27px;
    background: var(--brand-red);
  }

  /* Back cards */
  .back-brand {
    position: absolute;
    left: 0;
    right: 0;
    top: 92px;
    display: flex;
    justify-content: center;
    align-items: center;
    gap: 12px;
  }
  .back-brand__name {
    font-weight: 700;
    font-size: 56px;
    letter-spacing: -1px;
  }
  .back-brand__mark {
    width: 30px;
    height: 30px;
  }
  .back-url {
    position: absolute;
    left: 0;
    right: 0;
    top: 252px;
    text-align: center;
    font-weight: 500;
    font-size: 15px;
    letter-spacing: 3.2px;
  }
  .card--back-white .back-brand__name { color: var(--brand-red); }
  .card--back-white .back-brand__mark { background: var(--brand-red); }
  .card--back-white .back-url { color: var(--ink); top: 262px; }
  .card--back-red .back-brand__name,
  .card--back-black .back-brand__name { color: var(--paper); }
  .card--back-red .back-brand__mark,
  .card--back-black .back-brand__mark { background: var(--paper); }
  .card--back-red .back-url,
  .card--back-black .back-url { color: var(--paper); }
</style>
</head>
<body>
<main class="canvas">

  <section class="card card--front">
    <div class="brand">
      <span class="brand__mark"></span>
      <span class="brand__name">LorvanTest</span>
    </div>
    <div class="divider"></div>
    <div class="contact">
      <h2 class="contact__name">Todd Merrick</h2>
      <ul class="contact__list">
        <li class="contact__item">
          <svg class="contact__icon" viewBox="0 0 12 12" aria-hidden="true"><path d="M3 1 L5 3.6 L3.9 4.9 Q5 7.2 7.1 8.1 L8.4 7 L11 9 L9.8 11 Q4.5 10.8 1 3 Z" fill="#ec1c24"/></svg>
          877-514-9073 ext. 318
        </li>
        <li class="contact__item">
          <svg class="contact__icon" viewBox="0 0 12 12" aria-hidden="true"><rect x="0.5" y="2.5" width="11" height="7.5" fill="#ec1c24"/><path d="M0.8 2.8 L6 6.8 L11.2 2.8" fill="none" stroke="#fff" stroke-width="1"/></svg>
          Todd@lorvantest.com
        </li>
        <li class="contact__item">
          <svg class="contact__icon" viewBox="0 0 12 12" aria-hidden="true"><circle cx="6" cy="6" r="5.2" fill="#ec1c24"/><path d="M1 6 H11 M6 0.8 Q3 6 6 11.2 M6 0.8 Q9 6 6 11.2" fill="none" stroke="#fff" stroke-width="0.8"/></svg>
          www.LorvanTest.com
        </li>
      </ul>
    </div>
    <div class="front-rule"></div>
    <div class="front-band"></div>
  </section>

  <section class="card card--back-white">
    <div class="back-brand">
      <span class="back-brand__name">LorvanTest</span>
      <span class="back-brand__mark"></span>
    </div>
    <p class="back-url" style="margin:0">www.LorvanTest.com</p>
  </section>

  <section class="card card--back-red">
    <div class="back-brand">
      <span class="back-brand__name">LorvanTest</span>
      <span class="back-brand__mark"></span>
    </div>
    <p class="back-url" style="margin:0">www.LorvanTest.com</p>
  </section>

  <section class="card card--back-black">
    <div class="back-brand">
      <span class="back-brand__name">LorvanTest</span>
      <span class="back-brand__mark"></span>
    </div>
    <p class="back-url" style="margin:0">www.LorvanTest.com</p>
  </section>

</main>
</body>
</html>
```